International Trade Consulting Firm Seeks Quality Newsletter Design

Our company provides consulting services to Pinnacle 300 type companies. We compete with the largest consulting companies in the world. However, we have the highest level of expertise in the industry and need to look the most professional and high end. We have very relevant and important information to provide our customers about their compliance and projects. We will have the winning design coded to be an e-newsletter, so it needs to be one page. We want to keep our company colors and logo design in the newsletter, they are attached. We DO NOT want it to look like a mini-version of our website. We want a fresh look to this marketing piece. Newsletter will need to include title, possible sub-heading, space for a feature story, 2 other stories included, and space on either the left or right for short cuts, links or highlights of other articles. Contents/'In this issue' section, about us or branding area, section for relevant links, etc...
Pinnacle 300 companies, High-level management
Marketing

```html
<!DOCTYPE html>
<html lang="en">
<head>
<meta charset="utf-8">
<title>Keystone Trade Newsletter – 16 April 2014</title>
<link rel="stylesheet" href="https://fonts.googleapis.com/css2?family=Roboto+Condensed:wght@700&family=Arimo:wght@400;700&display=swap">
<style>
  :root{
    --backdrop:#979797;
    --paper:#ffffff;
    --ink:#2b2b2b;
    --heading:#1d4a1d;
    --accent:#a99a2b;
    --rule:#d3cc8e;
    --highlight:#fbf59c;
    --dark:#323232;
    --dark-soft:#3f3f3f;
    --brand-tint:#e4ec9e;
  }
  *{box-sizing:border-box;margin:0;padding:0}
  html,body{width:1200px;height:900px;overflow:hidden}
  body{background:var(--backdrop);font-family:"Arimo",Arial,sans-serif;color:var(--ink);position:relative}
  .page{position:absolute;width:522px;background:var(--paper);overflow:hidden;box-shadow:0 2px 8px rgba(0,0,0,.25)}
  .page--left{left:63px;top:20px;height:880px}
  .page--right{left:620px;top:0;height:885px}
  .abs{position:absolute}

  .heading{font-family:"Roboto Condensed","Arial Narrow",sans-serif;font-weight:700;color:var(--heading);text-transform:uppercase;letter-spacing:0}
  .heading--xl{font-size:34px;line-height:40px}
  .heading--lg{font-size:26px;line-height:31px}
  .body-copy{font-size:11px;line-height:18px}
  .body-copy p{margin:0}

  .cta{position:absolute;display:block;width:96px;height:23px}
  .read-more{position:absolute;left:0;top:0;width:96px;height:23px;display:flex;align-items:center;justify-content:center;padding-left:6px;font-size:11px;color:var(--heading);border:1px solid var(--accent);letter-spacing:.3px;text-decoration:none}
  .cta svg{position:absolute;left:0;top:0}

  /* sidebar */
  .sidebar{position:absolute;left:0;top:0;width:174px;height:100%;border-right:1px solid var(--rule)}
  .brand-block{position:absolute;left:0;top:0;width:174px;height:208px;background:linear-gradient(180deg,#1c2a30 0%,#243a40 55%,#2f5556 80%,#3a6460 100%)}
  .brand-name{position:absolute;left:23px;top:56px;display:flex;align-items:center;gap:8px;font-family:"Arimo",sans-serif;font-weight:400;font-size:15px;color:#ffffff}
  .brand-mark{width:12px;height:12px;background:#ffffff}
  .brand-intro{position:absolute;left:23px;top:132px;width:135px;font-size:9px;line-height:14.5px;color:var(--brand-tint)}
  .brand-intro u{text-decoration:underline}
  .social-bar{position:absolute;left:0;top:208px;width:174px;height:34px;background:var(--dark-soft);display:flex;align-items:center;justify-content:space-around;padding:0 16px}
  .social-dot{width:13px;height:13px;border-radius:50%;background:#e6e6e6}
  .site-url{position:absolute;left:0;top:249px;width:174px;text-align:center;font-size:10px;font-weight:700;letter-spacing:1.3px;color:#444}
  .issue-menu{position:absolute;left:0;top:270px;width:174px;border-top:1px solid var(--rule);border-bottom:1px solid var(--rule)}
  .issue-item{padding:10px 12px 5px 23px;height:48px}
  .issue-item--featured{background:var(--highlight)}
  .issue-item h3{font-family:"Roboto Condensed",sans-serif;font-weight:700;font-size:12.5px;color:var(--heading);line-height:13px}
  .issue-item p{font-size:7px;line-height:9px;color:#333}
  .profile{position:absolute;left:0;top:474px;width:174px}
  .profile-photo{position:absolute;left:23px;top:20px;width:66px;height:66px;border-radius:50%;border:2px solid #333;background:radial-gradient(circle at 50% 45%,#c9a285 0%,#9c7a63 45%,#e7e2dc 75%)}
  .profile-name{position:absolute;left:98px;top:42px;font-family:"Roboto Condensed",sans-serif;font-weight:700;font-size:10px;color:var(--heading);line-height:11px}
  .profile-name span{display:block;font-family:"Arimo",sans-serif;font-weight:400;font-size:9px}
  .profile-text{position:absolute;left:23px;top:95px;width:135px;font-size:8.4px;line-height:14.4px}
  .profile-text p+p{margin-top:13px}
  .section-rule{position:absolute;left:0;width:174px;border-top:1px solid var(--rule)}
  .section-label{position:absolute;left:23px;font-family:"Roboto Condensed",sans-serif;font-weight:700;font-size:12px;color:var(--heading)}
  .info-item{position:absolute;left:23px;width:140px}
  .info-item h4{font-size:8.4px;font-weight:700;color:#222;line-height:12px}
  .info-item p{font-size:8.4px;line-height:14.3px;color:#333}
  .icon{position:absolute}

  /* main columns */
  .main{position:absolute;left:174px;top:0;width:348px;height:100%}
  .photo{position:absolute}
  .date-tag{position:absolute;display:flex;align-items:center;gap:6px;font-size:10px;color:#333;letter-spacing:.5px}
  .date-tag b{font-weight:700}
  .story-label{position:absolute;height:22px;padding:0 14px 0 22px;background:var(--dark);color:var(--highlight);font-size:11px;display:flex;align-items:center;letter-spacing:.3px;clip-path:polygon(10px 0,100% 0,100% 100%,10px 100%,0 50%)}
  .subheading{display:flex;align-items:center;gap:7px;font-size:10px;font-weight:700;color:var(--heading);letter-spacing:.3px}

  .link-list{position:absolute;left:23px;top:398px;list-style:none}
  .link-list li{display:flex;align-items:center;gap:6px;font-size:8px;height:20.5px;color:#333}
  .tag-cloud{position:absolute;left:23px;top:588px;width:140px;color:var(--heading);font-weight:700;line-height:17px}
  .tag-cloud span{display:inline-block;margin-right:2px}
  .t-s{font-size:7px}
  .t-m{font-size:10px}
  .t-l{font-size:16px}
  .t-xl{font-size:18px}
  .t-u{text-decoration:underline}

  .feature-panel{position:absolute;left:0;top:68px;width:347px;height:350px;background:var(--highlight)}
  .two-col{position:absolute;left:15px;top:94px;width:318px;column-count:2;column-gap:18px;font-size:10.3px;line-height:15.4px}
  .two-col p+p{margin-top:15px}

  .wrap-photo{float:left;width:136px;height:136px;border-radius:50%;border:2px solid #333;margin:0 14px 6px 0;background:radial-gradient(circle at 50% 45%,#d9a98a 0%,#b07a5e 35%,#8a5a48 55%,#e2d8cc 80%)}
  .page-footer{position:absolute;left:0;bottom:3px;width:522px;height:54px;background:var(--dark);display:flex;align-items:center;padding:0 18px;color:var(--highlight);font-size:8.5px;letter-spacing:.5px}
  .page-footer b{font-weight:700}
  .footer-social{margin-left:auto;display:flex;gap:20px;padding-right:6px}
  .footer-social i{display:block;width:14px;height:14px;border-radius:50%;background:#e6e6e6}
</style>
</head>
<body>

<article class="page page--left">
  <aside class="sidebar">
    <div class="brand-block" role="img" aria-label="Darkened beach photo behind the company name">
      <div class="brand-name"><i class="brand-mark"></i>Keystone Trade</div>
      <p class="brand-intro">Editaquos rem restis dis imoditi ossitat urestius aut aut <u>pariberum</u> faccus <u>doloribus</u> aut prem repedis et eosam fuga.</p>
    </div>
    <div class="social-bar"><i class="social-dot"></i><i class="social-dot"></i><i class="social-dot"></i><i class="social-dot"></i></div>
    <div class="site-url">www.ktrcorp.com</div>

    <nav class="issue-menu">
      <div class="issue-item"><h3>ARTICLE 1</h3><p>Editaquos rem restis dis imoditi ossitat aut aut pariberum fuga.</p></div>
      <div class="issue-item"><h3>ARTICLE 2</h3><p>Editaquos rem restis dis imoditi ossitat aut aut pariberum fuga.</p></div>
      <div class="issue-item issue-item--featured"><h3>FEATURED STORY</h3><p>Editaquos rem restis dis imoditi ossitat aut aut pariberum fuga.</p></div>
      <div class="issue-item"><h3>ARTICLE 3</h3><p>Editaquos rem restis dis imoditi ossitat aut aut pariberum fuga.</p></div>
    </nav>

    <section class="profile">
      <div class="profile-photo" role="img" aria-label="Portrait photo of the CEO"></div>
      <div class="profile-name">DANIEL REYES<span>CEO</span></div>
      <div class="profile-text">
        <p>Editaquos rem restis dis imoditi ossitat urestius aut aut pariberum faccus doloribus aut prem repedis et eosam fuga. Giam quis quiae vel incid etur?</p>
        <p>Erchiliquo culparciame nobitates ma por rem exerrun tibusti doluptiore dipsuntus Iciendant id quossedit, ius consequia debit alit expellore sin erem vendita sperfernamus autetur?</p>
      </div>
    </section>

    <div class="section-rule" style="top:765px"></div>
    <div class="section-label" style="top:777px">ABOUT US</div>
    <svg class="icon" style="left:70px;top:800px" width="40" height="40" viewBox="0 0 40 40" fill="none" stroke="var(--accent)" stroke-width="2">
      <path d="M8 16h20v10a8 8 0 0 1-8 8h-4a8 8 0 0 1-8-8z"/><path d="M28 19h3a4 4 0 0 1 0 8h-3"/><path d="M14 6v6M19 4v8M24 6v6"/>
    </svg>
    <div class="info-item" style="top:855px"><h4>OMNIHILLES DERORRO VLAUT</h4><p>Accabor eperum esciasi</p></div>
  </aside>

  <div class="main">
    <div class="photo" style="left:0;top:0;width:348px;height:208px;background:linear-gradient(180deg,#5fb6e8 0%,#8ccdf0 35%,#6d5a44 55%,#4b3a2a 70%,#3fb3c4 85%,#e9dcc0 100%)" role="img" aria-label="Thatched beach hut against a blue sky and sea"></div>
    <div class="date-tag" style="left:226px;top:18px">
      <svg width="22" height="8" viewBox="0 0 22 8"><path d="M0 4h19M15 1l4 3-4 3" stroke="var(--accent)" stroke-width="1.6" fill="none"/></svg>
      <span><b>16 APRIL</b> 2014</span>
    </div>

    <h1 class="heading heading--xl abs" style="left:15px;top:222px;width:320px">Heading title of the article below</h1>
    <div class="body-copy abs" style="left:15px;top:308px;width:320px">
      <p>Lendae res nulpa cus, cum fugia volo quodipsus eiciis nullamus invera as et quiataq uoditin velent.</p>
      <p>Editaquos rem restis dis imoditi ossitat urestius aut aut pariberum faccus doloribus aut prem repedis et eosam fuga. It ipsum et quas dolorporiate natur se dolore eum ent modigen dandand anditate eicat apiet eicit omnis eum, arum evernat emquisti sus.</p>
      <p>Omnihilles derorro volo conse laut voloreh endite pre illa secabo.</p>
    </div>
    <div class="cta" style="left:15px;top:439px">
      <a class="read-more">READ MORE</a>
      <svg width="10" height="23" viewBox="0 0 10 23"><path d="M0 0l9 11.5L0 23" fill="var(--paper)" stroke="var(--accent)" stroke-width="1"/></svg>
    </div>

    <h2 class="heading heading--lg abs" style="left:15px;top:491px;width:320px">Smaller heading title for longer title text</h2>
    <div class="subheading abs" style="left:15px;top:558px">
      <svg width="22" height="8" viewBox="0 0 22 8"><path d="M0 4h19M15 1l4 3-4 3" stroke="var(--accent)" stroke-width="1.6" fill="none"/></svg>HERE IS POSSIBLE SUBHEADING</div>
    <div class="body-copy abs" style="left:15px;top:579px;width:320px">
      <p>Lendae res nulpa cus, cum fugia volo quodipsus eiciis nullamus invera as et quiataq uoditin velent.</p>
      <p>Editaquos rem restis dis imoditi ossitat urestius aut aut pariberum faccus doloribus aut prem repedis et eosam fuga. It ipsum et quas dolorporiate natur se dolore eum ent modigen dandand anditate eicat apiet eicit omnis eum, arum evernat emquisti sus.</p>
      <p>Omnihilles derorro volo conse laut voloreh endite pre illa secabo.</p>
    </div>
    <div class="cta" style="left:15px;top:708px">
      <a class="read-more">READ MORE</a>
      <svg width="10" height="23" viewBox="0 0 10 23"><path d="M0 0l9 11.5L0 23" fill="var(--paper)" stroke="var(--accent)" stroke-width="1"/></svg>
    </div>

    <div class="photo" style="left:0;top:767px;width:348px;height:113px;background:linear-gradient(90deg,#9a8d7a 0%,#c9bfae 30%,#5d6a6c 55%,#b8a590 80%,#7d6a58 100%)" role="img" aria-label="Team of colleagues talking in an office"></div>
    <div class="story-label" style="left:17px;top:857px">FEATURED STORY</div>
  </div>

  <svg class="icon" style="left:165px;top:752px" width="34" height="34" viewBox="0 0 34 34">
    <path d="M17 1l4.7 10.3 11.3 1.2-8.5 7.6 2.4 11.1L17 25.5 7.1 31.2l2.4-11.1L1 12.5l11.3-1.2z" fill="#f0e86a" stroke="#c9bb3a" stroke-width="1"/>
  </svg>
</article>

<article class="page page--right">
  <aside class="sidebar" style="height:828px">
    <svg class="icon" style="left:66px;top:-18px" width="40" height="40" viewBox="0 0 40 40" fill="none" stroke="var(--accent)" stroke-width="2">
      <path d="M8 16h20v10a8 8 0 0 1-8 8h-4a8 8 0 0 1-8-8z"/><path d="M28 19h3a4 4 0 0 1 0 8h-3"/>
    </svg>
    <div class="info-item" style="top:31px"><h4>OMNIHILLES DERORRO VLAUT</h4><p>Accabor eperum esciasi maionemquo excea volupta tibusam, et aut es ut impellu ptiusam est, offictate volorec</p></div>
    <svg class="icon" style="left:75px;top:110px" width="30" height="52" viewBox="0 0 30 52" fill="none" stroke="var(--accent)" stroke-width="2">
      <path d="M15 50C6 34 2 26 2 15a13 13 0 0 1 26 0c0 11-4 19-13 35z"/><circle cx="15" cy="15" r="5"/>
    </svg>
    <div class="info-item" style="top:166px"><h4>DERORRO OMNIHILLES VLAUT</h4><p>Accabor eperum esciasi maionemquo excea volupta tibusam, et aut es ut impellu ptiusam est, offictate volorec</p></div>
    <svg class="icon" style="left:67px;top:248px" width="44" height="44" viewBox="0 0 44 44" fill="none" stroke="var(--accent)" stroke-width="2">
      <circle cx="22" cy="22" r="20"/><path d="M12 22l7 7 13-14"/>
    </svg>
    <div class="info-item" style="top:299px"><h4>VLAUT OMNIHILLES DERORRO</h4><p>Accabor eperum esciasi maionemquo excea volupta tibusam, et aut es ut impellu ptiusam est, offictate volorec</p></div>

    <div class="section-rule" style="top:387px"></div>
    <ul class="link-list">
      <li><svg width="22" height="8" viewBox="0 0 22 8"><path d="M0 4h19M15 1l4 3-4 3" stroke="var(--accent)" stroke-width="1.6" fill="none"/></svg>Links to Other Resources</li>
      <li><svg width="22" height="8" viewBox="0 0 22 8"><path d="M0 4h19M15 1l4 3-4 3" stroke="var(--accent)" stroke-width="1.6" fill="none"/></svg>www.examplesite.org</li>
      <li><svg width="22" height="8" viewBox="0 0 22 8"><path d="M0 4h19M15 1l4 3-4 3" stroke="var(--accent)" stroke-width="1.6" fill="none"/></svg>Links to Other Resources</li>
      <li><svg width="22" height="8" viewBox="0 0 22 8"><path d="M0 4h19M15 1l4 3-4 3" stroke="var(--accent)" stroke-width="1.6" fill="none"/></svg>www.examplesite.org</li>
      <li><svg width="22" height="8" viewBox="0 0 22 8"><path d="M0 4h19M15 1l4 3-4 3" stroke="var(--accent)" stroke-width="1.6" fill="none"/></svg>Links to Other Resources</li>
      <li><svg width="22" height="8" viewBox="0 0 22 8"><path d="M0 4h19M15 1l4 3-4 3" stroke="var(--accent)" stroke-width="1.6" fill="none"/></svg>www.examplesite.org</li>
      <li><svg width="22" height="8" viewBox="0 0 22 8"><path d="M0 4h19M15 1l4 3-4 3" stroke="var(--accent)" stroke-width="1.6" fill="none"/></svg>www.examplesite.org</li>
      <li><svg width="22" height="8" viewBox="0 0 22 8"><path d="M0 4h19M15 1l4 3-4 3" stroke="var(--accent)" stroke-width="1.6" fill="none"/></svg>Links to Other Resources</li>
    </ul>
    <div class="section-rule" style="top:572px"></div>
    <div class="tag-cloud">
      <span class="t-m">Tags</span> <span class="t-s t-u">CEO</span> <span class="t-l">Marketing</span><br>
      <span class="t-s">Finance</span> <span class="t-m">Team</span> <span class="t-s">Success</span> <span class="t-m">Tags</span><br>
      <span class="t-l">CEO</span> <span class="t-s t-u">Marketing</span> <span class="t-m">Finance</span><br>
      <span class="t-l t-u">Team</span> <span class="t-s">Success</span> <span class="t-m">Tags</span> <span class="t-s">CEO</span><br>
      <span class="t-s">Marketing</span> <span class="t-l">Finance</span><br>
      <span class="t-m">Team</span> <span class="t-s t-u">Success</span> <span class="t-xl">Tags</span>
    </div>
  </aside>

  <div class="main" style="height:828px">
    <div class="photo" style="left:0;top:0;width:348px;height:68px;background:linear-gradient(90deg,#6b5a4a 0%,#b9ad9a 35%,#d8d2c6 60%,#8a6f5a 100%)" role="img" aria-label="Colleagues working together in an office"></div>
    <div class="story-label" style="left:18px;top:34px">FEATURED STORY</div>

    <section class="feature-panel">
      <h2 class="heading heading--xl abs" style="left:15px;top:6px;width:320px">Heading title of the article below</h2>
      <div class="two-col">
        <p>Lendae res nulpa cus, cum fugia volo quodipsus eiciis nullamus invera as et quiataq uoditin velent.</p>
        <p>Editaquos rem restis dis imoditi ossitat urestius aut aut pariberum faccus doloribus aut prem repedis et eosam fuga. It ipsum et quas dolorporiate natur se dolore eum ent modigen dandand anditate eicat apiet eicit omnis eum, arum evernat emquisti sus.<br>Omnihilles derorro volo conse laut voloreh endite pre illa secabo. To tenis endantur, aut quodis estis et earia corest, a sin consedi quia quam um nullent officit voluptam cus experestis intiur autes sequi ut repelec totaspelenis nimus, to con cor arunditias et audit quat.</p>
        <p>Vit etum qui cone volupta sed mi, is et autem veles cus expelisin nobit assus nitatem autem verumqui volumet voluptaeptas exerumquiae. Dae magnam sum aut landundit quam eost quis si dipsa</p>
      </div>
    </section>

    <h2 class="heading heading--xl abs" style="left:15px;top:446px;width:320px">Article with image inside text</h2>
    <div class="body-copy abs" style="left:15px;top:531px;width:320px;line-height:17.9px">
      <div class="wrap-photo" role="img" aria-label="Portrait photo of a smiling child"></div>
      <p>Lendae res nulpa cus, cum fugia volo quodipsus eiciis nullamus invera as et quiataq uoditin velent. Editaquos rem restis dis imoditi ossitat urestius aut aut pariberum faccus doloribus aut prem repedis et eosam fuga. It ipsum et quas dolorporiate natur se dolore eum ent modigen dandand anditate eicat apiet eicit omnis eum, arum evernat emquisti sus. It ipsum et quas dolorporiate natur se dolore eum ent modigen dandand anditate eicat apiet eicit omnis eum, arum evernat emquisti sus.</p>
      <p>Omnihilles derorro volo conse laut voloreh endite pre illa secabo.</p>
    </div>
    <div class="cta" style="left:15px;top:769px">
      <a class="read-more">READ MORE</a>
      <svg width="10" height="23" viewBox="0 0 10 23"><path d="M0 0l9 11.5L0 23" fill="var(--paper)" stroke="var(--accent)" stroke-width="1"/></svg>
    </div>
  </div>

  <footer class="page-footer">
    <span><b>16 APRIL</b> 2014</span>
    <span style="margin-left:155px">www.ktrcorp.com</span>
    <span class="footer-social"><i></i><i></i><i></i><i></i></span>
  </footer>
</article>

</body>
</html>
```